Website for Architecture & Interior Design firm

We are architecture and interior design firm looking for website design, word press based, smooth, elegant and easy to use for visitors. It should be easy to navigate using a mobile phone, with the ability to change pictures easily. It is a Bilingual website, (English: left to right, Arabic: right to left). A button in the menu bar is required to change the language, At first, we expect an English version, then we will help the designer by providing Arabic translation for any part of the website. Our website main purpose is to display our works in a picture format (Portfolio) to our clients, which mainly consist of four galleries from our (Services) as follow: 1- Architecture 2- Interior Design 3- Project Management 4- Importing from Abroad - Each service will have its page, which displays projects(items) in thumbnail format with simple text, which deploys (when clicked) into Fullscreen gallery to show the items related pictures (Dark gray or black background). - Navigation buttons/arrows are required, (X) button to close the navigation. - This is a very important part, the user experience in PC/Browser mode or Mobile mode should be easy, error-free and fast. Our homepage consists of four main elements: A- Edge to edge picture (Changing in a smooth transitional way, Random pictures from our Services) with our Logo, also persistent menu bar in the top (Home | About Us | Architecture | Interior design | Project Management | Importing from Abroad) + Social media icons B- Photo tiles (Random pictures from our Services) C- Our Services in a fixed 4-tile picture (Clickable) D- Contact Section (Simple name, contact number, message form) We expect the final service should be: 1- a fully functioning website, WordPress based, ready to be used by visitors 2- full content filling, we will contact the designer and provide the material (texture, text,etc..)
Colors
Designer to choose colors to be used in the design.
Look and feel
Each slider illustrates characteristics of the customer's brand and the style your logo design should communicate.

```html
<!DOCTYPE html>
<html lang="en">
<head>
<meta charset="utf-8">
<title>K &amp; M Designs — Architecture Gallery</title>
<link rel="stylesheet" href="https://fonts.googleapis.com/css2?family=Montserrat:wght@400;500;600;700&display=swap">
<style>
  :root {
    --ink: #1c1c1e;
    --muted: #55575c;
    --white: #ffffff;
    --hero-top: #4a5566;
    --hero-mid: #6f7684;
    --hero-low: #3b4250;
    --accent: #2f6fb8;
    --overlay: rgba(30, 90, 170, 0.82);
    --rule: #d9d9d9;
  }
  * { box-sizing: border-box; margin: 0; padding: 0; }
  html, body { width: 741px; height: 1200px; overflow: hidden; background: var(--white); }
  body { font-family: "Montserrat", Arial, sans-serif; color: var(--ink); position: relative; }

  .hero {
    position: absolute; left: 0; top: 0; width: 741px; height: 268px;
    background: linear-gradient(180deg, var(--hero-top) 0%, var(--hero-mid) 45%, #8a8f97 70%, var(--hero-low) 100%);
  }
  .topbar { position: absolute; left: 0; top: 0; width: 100%; height: 60px; }
  .social { position: absolute; left: 98px; top: 14px; display: flex; gap: 14px; }
  .social span { width: 9px; height: 9px; border-radius: 50%; background: var(--white); display: block; }
  .main-nav { position: absolute; left: 96px; top: 44px; display: flex; gap: 28px; }
  .main-nav a { color: var(--white); text-decoration: none; font-size: 9.5px; font-weight: 600; letter-spacing: .3px; padding-bottom: 6px; }
  .main-nav a.is-current { border-bottom: 2px solid var(--white); }
  .lang-switch {
    position: absolute; left: 690px; top: 20px; width: 30px; height: 14px;
    border: 1px solid var(--white); color: var(--white); font-size: 6.5px; font-weight: 600;
    display: flex; align-items: center; justify-content: space-between; padding: 0 3px;
  }

  .brand { position: absolute; left: 0; top: 112px; width: 100%; text-align: center; color: var(--white); }
  .brand-mark { width: 26px; height: 26px; border: 2px solid var(--white); margin: 0 auto 12px; }
  .brand-name { font-size: 17px; font-weight: 500; letter-spacing: 2px; }
  .brand-sub { font-size: 17px; font-weight: 500; letter-spacing: 2px; margin-top: 2px; }
  .brand-tag { font-size: 8px; font-weight: 500; letter-spacing: 2px; margin-top: 6px; }

  .gallery-title {
    position: absolute; left: 0; top: 362px; width: 100%; text-align: center;
    font-size: 21px; font-weight: 700; letter-spacing: .5px;
  }
  .gallery-grid {
    position: absolute; left: 35px; top: 418px; width: 672px;
    display: grid; grid-template-columns: repeat(3, 1fr); grid-auto-rows: 170px; gap: 10px;
  }
  .tile { position: relative; overflow: hidden; }
  .tile--a { background: linear-gradient(135deg, #2d5f9a, #6f94c3); }
  .tile--b { background: linear-gradient(160deg, #3c5d8a, #b58d62 60%, #6c5a48); }
  .tile--c { background: linear-gradient(150deg, #e9eef4, #8b97a6 60%, #39424f); }
  .tile--d { background: linear-gradient(180deg, #4d86c6, #9fbbd8 50%, #6d6e6f); }
  .tile--e { background: linear-gradient(180deg, #8fb5d6, #c3a985 65%, #7e6f5d); }
  .tile--f { background: linear-gradient(180deg, #26324a, #52607a 55%, #2a2f3a); }
  .tile--g { background: linear-gradient(135deg, #3c7cc8, #cdb87c 55%, #7c6a3a); }
  .tile--h { background: linear-gradient(160deg, #5a90cc, #c9ccd0 50%, #495260); }
  .tile--i { background: linear-gradient(180deg, #4d3f4a, #a46a5a 55%, #2e2a33); }

  .tile-overlay {
    position: absolute; inset: 0; background: var(--overlay); color: var(--white);
    display: flex; flex-direction: column; align-items: center; justify-content: center; text-align: center; padding: 0 26px;
  }
  .tile-overlay h3 { font-size: 13px; font-weight: 700; letter-spacing: .5px; margin-bottom: 6px; }
  .tile-overlay p { font-size: 8px; line-height: 1.35; margin-bottom: 12px; }
  .tile-button { border: 1px solid var(--white); font-size: 8px; font-weight: 700; padding: 5px 14px; }

  .more-arrow { position: absolute; left: 350px; top: 982px; }

  .site-footer { position: absolute; left: 0; top: 1043px; width: 100%; height: 157px; border-top: 1px solid var(--rule); }
  .footer-brand { position: absolute; left: 100px; top: 42px; font-size: 22px; line-height: 1.05; letter-spacing: .5px; }
  .footer-brand strong { font-weight: 700; display: block; }
  .footer-brand span { font-weight: 400; display: block; }
  .footer-links { position: absolute; top: 44px; list-style: none; }
  .footer-links li { font-size: 7.5px; font-weight: 600; line-height: 13px; }
  .footer-links--one { left: 254px; }
  .footer-links--two { left: 373px; }
  .footer-social { position: absolute; left: 537px; top: 46px; display: flex; gap: 12px; }
  .footer-social span { width: 8px; height: 8px; border-radius: 50%; background: var(--ink); display: block; }
  .footer-legal { position: absolute; left: 537px; top: 70px; font-size: 6.5px; color: var(--muted); line-height: 12px; }
</style>
</head>
<body>
  <header class="hero" role="img" aria-label="Dusk skyline of modern towers with palm trees in the foreground">
    <div class="topbar">
      <div class="social" aria-label="Social links"><span></span><span></span><span></span><span></span></div>
      <nav class="main-nav">
        <a href="#">ABOUT US</a>
        <a href="#" class="is-current">ARCHITECTURE</a>
        <a href="#">INTERIOR DESIGN</a>
        <a href="#">PROJECT MANAGEMENT</a>
        <a href="#">IMPORTING FROM ABROAD</a>
      </nav>
      <div class="lang-switch">ENG
        <svg width="5" height="4" viewBox="0 0 5 4"><path d="M0 0 L2.5 3 L5 0" fill="none" stroke="#fff" stroke-width="0.8"/></svg>
      </div>
    </div>
    <div class="brand">
      <div class="brand-mark"></div>
      <div class="brand-name">K &amp; M</div>
      <div class="brand-sub">DESIGN &amp; PROJECT</div>
      <div class="brand-tag">MANAGEMENT</div>
    </div>
  </header>

  <h2 class="gallery-title">ARCHITECTURE GALLERY</h2>

  <section class="gallery-grid">
    <div class="tile tile--a" role="img" aria-label="Modern building facade">
      <div class="tile-overlay">
        <h3>PROJECT TITLE</h3>
        <p>Lorem ipsum dolor sit amet, consectetuer adipiscing elit, aenean commodo ligula eget.</p>
        <span class="tile-button">CLICK HERE</span>
      </div>
    </div>
    <div class="tile tile--b" role="img" aria-label="Curved facade of a honeycomb-patterned tower"></div>
    <div class="tile tile--c" role="img" aria-label="Glass tower seen from below"></div>
    <div class="tile tile--d" role="img" aria-label="Business district towers under blue sky"></div>
    <div class="tile tile--e" role="img" aria-label="Aerial view of a city skyline"></div>
    <div class="tile tile--f" role="img" aria-label="City towers at night"></div>
    <div class="tile tile--g" role="img" aria-label="Building with diagonal lattice facade"></div>
    <div class="tile tile--h" role="img" aria-label="Tower with angular patterned exterior"></div>
    <div class="tile tile--i" role="img" aria-label="Illuminated skyline at dusk"></div>
  </section>

  <svg class="more-arrow" width="40" height="20" viewBox="0 0 40 20" aria-hidden="true">
    <path d="M2 3 L20 17 L38 3" fill="none" stroke="#333" stroke-width="2.5"/>
  </svg>

  <footer class="site-footer">
    <div class="footer-brand"><strong>K &amp; M</strong><span>DESIGNS</span></div>
    <ul class="footer-links footer-links--one">
      <li>HOME</li><li>ABOUT US</li><li>ARCHITECTURE</li><li>INTERIOR DESIGN</li>
    </ul>
    <ul class="footer-links footer-links--two">
      <li>PROJECT MANAGEMENT</li><li>IMPORTING FROM ABROAD</li><li>CONTACT US</li>
    </ul>
    <div class="footer-social" aria-label="Social links"><span></span><span></span><span></span><span></span></div>
    <div class="footer-legal">© 2019 Company Name<br>All right reserved &nbsp;|&nbsp; Privacy Policy</div>
  </footer>
</body>
</html>
```